Business card design Needed for new logo / Construction business, home extensions and new builds

We need a business card design using our new logo files which i will attach to this project :)

We are a small construction business specialising in home extensions, new builds and property development. We are very ambitious and would appreciate professional and elegant designs for our new business card.

Very serious about using the services on MakerQuarry and recently acquired our new logo from here :)

Please get involved, i will feedback when i can as i am very busy but can respond daily, thanks

Target Market(s)

People that want to build onto their houses, new building developments or adding too their existing property

Industry/Entity Type

Construction

Contact Information for Business Card

Renwick Tolliver Construction, Lionel Ashby (Managing Director), Tel 07822254961, email - info@renwick-tolliver, www.renwick-tolliver.co.uk

Colors

Designer to choose colors to be used in the design.

Requirements
Must have
• I like a deep grey on the back please. A lot of you have provided black from and back, try mixing things up a little. The black looks cool 😎 Thanks

```html
<!DOCTYPE html>
<html lang="en">
<head>
<meta charset="utf-8">
<title>Renwick Tolliver Construction – Business Card</title>
<link href="https://fonts.googleapis.com/css2?family=Montserrat:wght@400;500;700&display=swap" rel="stylesheet">
<style>
  :root {
    --backdrop: #161617;
    --card-grey: #2c2d2f;
    --card-white: #ffffff;
    --gold: #d9a63a;
    --gold-light: #f1cd6d;
    --gold-deep: #b9861f;
    --silver: #b9bcc0;
    --silver-light: #e6e8ea;
    --text-light: #f2f2f2;
  }
  html, body {
    margin: 0;
    padding: 0;
    width: 1200px;
    height: 689px;
    overflow: hidden;
    background: var(--backdrop);
    font-family: "Montserrat", Arial, sans-serif;
  }
  .canvas {
    position: relative;
    width: 1200px;
    height: 689px;
  }
  .card {
    position: absolute;
    top: 190px;
    width: 540px;
    height: 310px;
    border-radius: 18px;
    overflow: hidden;
    box-shadow: 0 14px 34px rgba(0,0,0,0.55);
  }
  .card-gold {
    left: 40px;
    background: linear-gradient(135deg, var(--gold-light) 0%, var(--gold) 45%, var(--gold-deep) 100%);
  }
  .card-grey { left: 620px; background: var(--card-grey); }
  .card-grey .shapes { position: absolute; inset: 0; width: 100%; height: 100%; }

  .mark {
    position: absolute;
    left: 34px;
    top: 38px;
    display: flex;
    align-items: center;
    gap: 8px;
  }
  .mark-square { width: 14px; height: 14px; background: var(--gold); }
  .mark-name {
    font-size: 12px;
    font-weight: 700;
    letter-spacing: 1.5px;
    color: var(--gold);
  }

  .person { position: absolute; left: 34px; top: 96px; }
  .person-name {
    margin: 0;
    font-size: 24px;
    font-weight: 700;
    letter-spacing: 1px;
    color: var(--gold);
    white-space: nowrap;
  }
  .person-title {
    margin: 2px 0 0;
    font-size: 13px;
    font-weight: 400;
    color: var(--text-light);
  }

  .contacts {
    position: absolute;
    left: 34px;
    top: 168px;
    margin: 0;
    padding: 0;
    list-style: none;
    font-size: 12.5px;
    color: var(--text-light);
  }
  .contacts li { display: flex; align-items: center; gap: 8px; margin-bottom: 5px; white-space: nowrap; }
  .contacts svg { width: 12px; height: 12px; flex: none; }

  .address {
    position: absolute;
    left: 54px;
    top: 244px;
    margin: 0;
    font-style: normal;
    font-size: 12.5px;
    line-height: 1.45;
    color: var(--text-light);
  }

  .brand {
    position: absolute;
    left: 330px;
    top: 118px;
    width: 190px;
    margin: 0;
    text-align: center;
    font-size: 15px;
    font-weight: 700;
    letter-spacing: 1.5px;
    line-height: 1.4;
    color: var(--gold);
  }
</style>
</head>
<body>
<main class="canvas">
  <section class="card card-gold" role="img" aria-label="Embossed repeating pattern of the company mark on gold"></section>

  <section class="card card-grey">
    <svg class="shapes" viewBox="0 0 540 310" preserveAspectRatio="none" aria-hidden="true">
      <defs>
        <linearGradient id="goldSweep" x1="0" y1="0" x2="1" y2="1">
          <stop offset="0" stop-color="#b9861f"/>
          <stop offset="0.5" stop-color="#f1cd6d"/>
          <stop offset="1" stop-color="#c8952c"/>
        </linearGradient>
        <linearGradient id="silverSweep" x1="0" y1="0" x2="0" y2="1">
          <stop offset="0" stop-color="#e6e8ea"/>
          <stop offset="1" stop-color="#9ea2a6"/>
        </linearGradient>
      </defs>
      <path d="M300 0 C262 90 268 220 390 310 L540 310 L540 0 Z" fill="url(#silverSweep)"/>
      <path d="M282 150 C284 220 320 270 372 310 L420 310 C350 270 300 230 282 150 Z" fill="url(#goldSweep)"/>
      <path d="M312 0 C276 92 284 218 420 310 L540 310 L540 0 Z" fill="#ffffff"/>
    </svg>

    <div class="mark">
      <span class="mark-square"></span>
      <span class="mark-name">RENWICK TOLLIVER</span>
    </div>

    <div class="person">
      <h1 class="person-name">OWEN HARTLEY</h1>
      <p class="person-title">Managing Director</p>
    </div>

    <ul class="contacts">
      <li>
        <svg viewBox="0 0 12 12"><path d="M2.5 1 L4.5 1 L5.2 3.6 L4 4.6 C4.6 6 6 7.4 7.4 8 L8.4 6.8 L11 7.5 L11 9.5 C11 10.4 10.4 11 9.5 11 C5 11 1 7 1 2.5 C1 1.6 1.6 1 2.5 1 Z" fill="#d9a63a"/></svg>
        123 456 789
      </li>
      <li>
        <svg viewBox="0 0 12 12"><rect x="0.5" y="2.5" width="11" height="7.5" rx="1" fill="#d9a63a"/><path d="M1 3 L6 7 L11 3" stroke="#2c2d2f" stroke-width="1" fill="none"/></svg>
        info@yourgmail.com
      </li>
      <li>
        <svg viewBox="0 0 12 12"><circle cx="6" cy="6" r="5.2" fill="#d9a63a"/><path d="M0.8 6 H11.2 M6 0.8 C3.8 3 3.8 9 6 11.2 M6 0.8 C8.2 3 8.2 9 6 11.2" stroke="#2c2d2f" stroke-width="0.8" fill="none"/></svg>
        www.yourwebsite.com
      </li>
    </ul>

    <address class="address">Your address, City<br>State, Zip 1234</address>

    <p class="brand">RENWICK TOLLIVER<br>CONSTRUCTION</p>
  </section>
</main>
</body>
</html>
```